CREATE A BUSINESS CARD FOR A BOAT CLEANING SERVICE

WE ARE STARTING A NEW BOAT CLEANING BUSINESS. WE DIVE UNDERWATER TO CLEAN BOAT HULLS, JETTIES, UNDERWATER STRUCTURES ETC. WE ARE LOOKING FOR AN UPPERMARKET MODERN LOGO AND BUSINESS CARD AS ALOT OF OUR TARGET MARKET WILL BE HIGH END. YOU HAVE TO DESIGN A BUSINESS CARD AND LOGO SEPERATELY .
THE BUSINESS CARD DIMESNION MUST BE STANDARD SIZE.
The standard dimensions of a printed business card are 3.5 x 2 inches

Target Market(s)

UNDERWATER SERVICED

Industry/Entity Type

Business

Contact Information for Business Card

HOLLAND UNDERWATER SERVICES

Font styles to use
Serif

Colors

Designer to choose colors to be used in the design.

Requirements
Must have
• HOLLAND
Nice to have
• dark
Should not have
• more than 3 colors

```html
<!DOCTYPE html>
<html lang="en">
<head>
<meta charset="utf-8">
<title>Holland Underwater Services – Business Card</title>
<link rel="stylesheet" href="https://fonts.googleapis.com/css2?family=Montserrat:wght@300;400;500&family=Roboto:wght@300;400;500&display=swap">
<style>
  :root {
    --page-bg: #e9e7e3;
    --card-bg: #fbfbfb;
    --brand-blue: #1f6aa5;
    --text-grey: #8a8d90;
    --rule-grey: #c9cbcd;
  }
  * { margin: 0; padding: 0; box-sizing: border-box; }
  html, body { width: 1200px; height: 1023px; overflow: hidden; background: var(--page-bg); }
  .card {
    position: absolute; left: 75px; top: 211px; width: 1050px; height: 600px;
    background: linear-gradient(160deg, #ffffff 0%, var(--card-bg) 60%, #f0f1f2 100%);
    border-radius: 22px; overflow: hidden;
    box-shadow: 0 18px 40px rgba(0,0,0,.18);
    font-family: "Roboto", sans-serif;
  }
  .card-band { position: absolute; left: 0; bottom: 0; width: 1050px; height: 110px; }
  .brand { position: absolute; left: 70px; top: 95px; }
  .brand-row { display: flex; align-items: center; gap: 22px; }
  .brand-dot { width: 58px; height: 58px; border-radius: 50%; background: var(--brand-blue); }
  .brand-name {
    font-family: "Montserrat", sans-serif; font-weight: 400; font-size: 46px;
    letter-spacing: 26px; color: var(--brand-blue);
  }
  .brand-tag {
    margin: 12px 0 0 80px; font-family: "Montserrat", sans-serif; font-weight: 300;
    font-size: 19px; letter-spacing: 9px; color: var(--text-grey);
  }
  .badges { position: absolute; left: 150px; top: 280px; display: flex; gap: 26px; align-items: center; }
  .badge-round { width: 62px; height: 62px; border-radius: 50%; background: #7fb0c9; }
  .badge-square { width: 62px; height: 62px; border-radius: 8px; background: #3b3f44; }
  .divider { position: absolute; left: 350px; top: 322px; width: 640px; height: 2px; background: var(--brand-blue); }
  .person { position: absolute; right: 60px; top: 228px; text-align: right; }
  .person-name { font-size: 40px; font-weight: 500; color: var(--brand-blue); letter-spacing: 1px; }
  .person-title { font-size: 19px; font-weight: 300; color: var(--text-grey); margin-top: 2px; }
  .address { position: absolute; right: 60px; top: 345px; text-align: right; font-size: 21px; font-weight: 300; color: var(--text-grey); line-height: 1.45; }
  .contacts { position: absolute; left: 350px; top: 345px; list-style: none; font-size: 21px; font-weight: 300; color: var(--text-grey); line-height: 1.5; }
  .contacts li { display: flex; align-items: center; gap: 12px; }
  .contacts svg { width: 14px; height: 14px; fill: none; stroke: var(--text-grey); stroke-width: 2; }
  .contacts .web { color: var(--brand-blue); font-weight: 400; }
</style>
</head>
<body>
  <div class="card">
    <svg class="card-band" viewBox="0 0 1050 110" aria-hidden="true">
      <path d="M0 102 L520 102 Q538 102 546 90 L560 70 Q568 58 586 58 L1050 58" stroke="var(--rule-grey)" stroke-width="6" fill="none"/>
      <path d="M0 110 L0 108 L528 108 Q548 108 558 94 L572 76 Q580 66 598 66 L1050 66 L1050 110 Z" fill="var(--brand-blue)"/>
    </svg>

    <div class="brand">
      <div class="brand-row">
        <div class="brand-dot"></div>
        <div class="brand-name">HOLLAND</div>
      </div>
      <div class="brand-tag">UNDERWATER SERVICES</div>
    </div>

    <div class="badges">
      <div class="badge-round" role="img" aria-label="Partner badge"></div>
      <div class="badge-square" role="img" aria-label="Certification badge"></div>
    </div>

    <div class="person">
      <div class="person-name">DANIEL HARPER</div>
      <div class="person-title">President</div>
    </div>
    <div class="divider"></div>
    <div class="address">300, 418- 9th Ave, SW<br>Calgary, AB T2P 1K4</div>

    <ul class="contacts">
      <li><svg viewBox="0 0 16 16"><path d="M4 2 L7 5 L5 7 Q7 10 9 11 L11 9 L14 12 L12 14 Q6 13 2 4 Z"/></svg>(410) 555-0182</li>
      <li><svg viewBox="0 0 16 16"><rect x="2" y="4" width="12" height="9"/><path d="M2 4 L8 9 L14 4"/></svg>info@hollandunderwater.com</li>
      <li class="web"><svg viewBox="0 0 16 16"><circle cx="8" cy="8" r="6"/><path d="M2 8 H14 M8 2 Q4 8 8 14 Q12 8 8 2"/></svg>www.hollandunderwater.com</li>
    </ul>
  </div>
</body>
</html>
```